Qorlant Business Card

We require a stunning business card for Qorlant - a new digital marketing agency. The logo provided was designed by a graphic designer here on Pixelfair.

www.qorlant.example - "Get more sales online"

What we do:
The business delivers website optimisation (Web design, social media strategy, digital strategies, SEO, PPC, conversion optimisation, email marketing) to get businesses more sales online.

The card must match the brand style which can be found on this website template:

http://layoutbazaar.example/item/gridmark-sharp-adaptive-allpurpose-theme/full_screen_preview/7301926

It must have 'wow' factor so that you'll never forget Qorlant - We're open to any materials, textures you think will work.

We don't want a boring run of the mill design - I can knock that up in Photoshop myself or use a template solution. It should be timeless and only need replacing should the contact details change.

The design should be eye catching, future proof, exceptionally chic, classy and oozing authority and confidence. Qorlant services must not look cheap.

Here's some brilliant designs to point you in the right direction:

http://tidyworks.example/30-remarkable-calling-cards/

The spec is for double sided, but we're open to your ideas. If it's going on an opaque or see through card, then of course a single side is preferable. Using creativity and thought on the medium for the card - shape - texture is desirable.

The strapline for the business is "Get more business online" please submit with / without strapline.
Updates

Please only submit your best 1-3 designs initially.

Target Market(s)

Business 2 Business - Local SMEs
Local professionals - Doctors, Dentists, Financials, Bespoke Retailers, Property companies - anyone with a decent budget to spend on digital marketing services and a high margin product or service to sell.

Industry/Entity Type

Graphic Designer

Requirements
Must have
• Text:
• name: Tom Calwayne
• position Digital Marketing Director
• mobile 07912 403 615
• website www.qorlant.example
Nice to have
• Check See http://tidyworks.example/30-remarkable-calling-cards/ for ideas.
• LinkedIn and Twitter usernames if there is space and it works on the design.

```html
<!DOCTYPE html>
<html lang="en">
<head>
<meta charset="utf-8">
<title>Qorlant Business Card</title>
<link href="https://fonts.googleapis.com/css2?family=Questrial&family=Open+Sans:wght@400;600&display=swap" rel="stylesheet">
<style>
  :root {
    --backdrop: #4a4b4d;
    --card-black: #1c1c1d;
    --card-charcoal: #2a2b2d;
    --card-white: #ececee;
    --brand-teal: #1f4a5a;
    --brand-red: #e8452c;
    --text-light: #e4e4e4;
    --texture: #141415;
  }
  * { margin: 0; padding: 0; box-sizing: border-box; }
  html, body { width: 1200px; height: 819px; overflow: hidden; }
  body {
    background: var(--backdrop);
    font-family: "Open Sans", Arial, sans-serif;
    position: relative;
  }
  .card {
    position: absolute;
    top: 260px;
    width: 520px;
    height: 298px;
    box-shadow: 0 14px 30px rgba(0,0,0,.35);
    overflow: hidden;
  }
  /* Front side */
  .card-front { left: 50px; background: var(--card-black); }
  .front-brand { position: absolute; left: 40px; top: 104px; }
  .wordmark {
    font-family: "Questrial", "Century Gothic", sans-serif;
    font-size: 46px; line-height: 1; letter-spacing: .5px;
  }
  .card-front .wordmark { color: var(--brand-red); }
  .strapline {
    font-family: "Questrial", "Century Gothic", sans-serif;
    font-size: 9px; margin-top: 6px; letter-spacing: .2px;
  }
  .card-front .strapline { color: var(--text-light); }
  .texture-panel {
    position: absolute; right: 34px; top: 34px;
    width: 210px; height: 230px;
    background: var(--texture);
  }
  /* Back side */
  .card-back { left: 630px; display: flex; }
  .back-brand-side {
    width: 57%; background: var(--card-white);
    display: flex; flex-direction: column; justify-content: center;
    padding-left: 38px;
  }
  .card-back .wordmark { color: var(--brand-teal); font-size: 44px; }
  .card-back .strapline { color: var(--brand-teal); }
  .back-contact-side {
    width: 43%; background: var(--card-charcoal);
    color: var(--text-light); padding: 58px 0 0 26px;
    font-size: 11px;
  }
  .person-name { color: var(--brand-red); font-weight: 600; font-size: 13px; }
  .person-role { font-size: 11px; margin-bottom: 16px; }
  .contact-list { list-style: none; }
  .contact-list li { display: flex; align-items: center; gap: 7px; margin-bottom: 3px; white-space: nowrap; }
  .contact-list svg { width: 10px; height: 10px; fill: var(--brand-red); flex: none; }
  .address { margin-top: 16px; line-height: 1.35; }
</style>
</head>
<body>
  <section class="card card-front" aria-label="Card front">
    <div class="front-brand">
      <div class="wordmark">Qorlant</div>
      <div class="strapline">Visibility on the internet for business websites</div>
    </div>
    <div class="texture-panel" role="img" aria-label="Raised spot-gloss texture decoration"></div>
  </section>

  <section class="card card-back" aria-label="Card back">
    <div class="back-brand-side">
      <div class="wordmark">Qorlant</div>
      <div class="strapline">Visibility on the internet for business websites</div>
    </div>
    <div class="back-contact-side">
      <p class="person-name">Tom Calwayne</p>
      <p class="person-role">Digital Marketing Director</p>
      <ul class="contact-list">
        <li><svg viewBox="0 0 10 10"><path d="M2 0.5 L3.6 2.6 L2.8 3.6 Q4 6 6.4 7.2 L7.4 6.4 L9.5 8 L8.4 9.5 Q3.5 9 0.5 1.6 Z"/></svg>01632 960 418</li>
        <li><svg viewBox="0 0 10 10"><rect x="2.5" y="0" width="5" height="10" rx="1"/><rect x="3.4" y="1.2" width="3.2" height="5.6" fill="#2a2b2d"/></svg>07912 403 615</li>
        <li><svg viewBox="0 0 10 10"><rect x="0" y="2" width="10" height="6.5" rx=".6"/><path d="M0.6 2.6 L5 6 L9.4 2.6" stroke="#2a2b2d" stroke-width="1" fill="none"/></svg>info@qorlant.example</li>
        <li><svg viewBox="0 0 10 10"><circle cx="5" cy="5" r="4.6"/><path d="M0.5 5 H9.5 M5 0.5 Q2.2 5 5 9.5 M5 0.5 Q7.8 5 5 9.5" stroke="#2a2b2d" stroke-width=".8" fill="none"/></svg>www.qorlant.example</li>
      </ul>
      <p class="address">Street name, city name,<br>zip code with country</p>
    </div>
  </section>
</body>
</html>
```